Structural Engineering Business Card

Brookvane Drafting does residential house plans for clients in Central Florida. Would like simple but elegant business card that is appropriate for a house plan engineering company. Prefer black business card with black/white them but open to other shades of blue. I uploaded a sample card that I came across that looked good but please come up with your own creative designs.

Contact Information for Business Card

Name, Title, Phone, Email, Address, website

```html
<!DOCTYPE html>
<html lang="en">
<head>
<meta charset="utf-8">
<title>Brookvane Drafting — Business Card</title>
<link href="https://fonts.googleapis.com/css2?family=Montserrat:wght@400;500;600;800&display=swap" rel="stylesheet">
<style>
  :root {
    --bg: #3a3330;
    --card: #232323;
    --card-back: #262626;
    --blue: #4cc3e6;
    --grey: #8e8e8e;
    --light: #e6e6e6;
  }
  * { box-sizing: border-box; margin: 0; padding: 0; }
  html, body { width: 1200px; height: 786px; overflow: hidden; background: var(--bg); }
  body { font-family: "Montserrat", sans-serif; position: relative; }

  .card {
    position: absolute;
    width: 540px;
    height: 309px;
    border-radius: 4px;
    overflow: hidden;
    box-shadow: 0 14px 30px rgba(0,0,0,.45);
  }
  .card--front { left: 40px; top: 238px; background: var(--card); }
  .card--back  { left: 620px; top: 238px; background: var(--card-back); }

  .brand-name {
    position: absolute;
    font-weight: 800;
    letter-spacing: .5px;
    color: var(--grey);
    white-space: nowrap;
  }
  .card--front .brand-name { left: 38px; top: 58px; font-size: 30px; }
  .card--back .brand-name { left: 0; right: 0; top: 118px; text-align: center; font-size: 34px; color: #5a5a5a; }

  .divider {
    position: absolute;
    left: 38px; right: 30px; top: 168px;
    height: 1px; background: var(--blue);
  }
  .person { position: absolute; left: 38px; top: 128px; }
  .person__name { font-size: 22px; font-weight: 600; color: var(--blue); line-height: 1.1; }
  .person__title { font-size: 12px; color: var(--light); }

  .address {
    position: absolute; right: 30px; top: 180px;
    text-align: right; font-size: 12px; line-height: 1.35; color: var(--light);
  }
  .contacts { position: absolute; left: 38px; top: 186px; list-style: none; }
  .contacts li {
    display: flex; align-items: center; gap: 10px;
    font-size: 13px; color: var(--light); line-height: 1.55;
  }
  .contacts svg { width: 11px; height: 11px; fill: var(--blue); flex: none; }

  .bands { position: absolute; left: 0; bottom: 0; width: 540px; height: 40px; }
  .back-strip { position: absolute; left: 0; right: 0; bottom: 34px; height: 7px; background: var(--blue); }
</style>
</head>
<body>
  <section class="card card--front" aria-label="Card front">
    <div class="brand-name">Brookvane Drafting</div>
    <div class="person">
      <div class="person__name">Dana Whitfield</div>
      <div class="person__title">Owner</div>
    </div>
    <div class="divider"></div>
    <div class="address">418 Larkspur Avenue<br>Orlando, FL 32803</div>
    <ul class="contacts">
      <li><svg viewBox="0 0 12 12"><path d="M2 1h3l1 3-2 1a7 7 0 0 0 3 3l1-2 3 1v3a1 1 0 0 1-1 1A10 10 0 0 1 1 2a1 1 0 0 1 1-1z"/></svg>+1 407 555 0182</li>
      <li><svg viewBox="0 0 12 12"><path d="M0 2h12v8H0z M0 2l6 4 6-4" fill="none" stroke="#4cc3e6" stroke-width="1.4"/></svg>info@brookvanedrafting.com</li>
      <li><svg viewBox="0 0 12 12"><circle cx="6" cy="6" r="5.5"/></svg>www.brookvanedrafting.com</li>
    </ul>
    <svg class="bands" viewBox="0 0 540 40" aria-hidden="true">
      <polygon points="330,18 540,18 540,30 318,30" fill="var(--grey)"/>
      <rect x="0" y="30" width="540" height="7" fill="var(--blue)"/>
    </svg>
  </section>

  <section class="card card--back" aria-label="Card back">
    <div class="brand-name">Brookvane Drafting</div>
    <div class="back-strip"></div>
  </section>
</body>
</html>
```